i would like a business card to leave with customers and potential customers for electrical work and for the supply and install of reverse cycle airconditioning in the domestic and commercial market.
I own my own business and im a sole trader. I have an a'class electrical lisence and also a refrigeration lisence so i am
able to offer complete installations in airconditioning by a fully qualified and lisenced tradesman.
im looking for something that comes across as unique and professional.
i had the coluor black and some gold in mind but open to any coluors.
something like Lanterra Electrical & Refrigeration
or Lanterra Air.
i will use this design on a business card to advertise through summer to help generate installs through the busy season.

Target Market(s)

Mainly domestic house holds through summer who are in need of airconditioning and reliable information to acomadate thier cooling and heating requirements

Industry/Entity Type

Electrical

Requirements
Must have
• Business name- Lanterra
My name- Mark Delford
My mobile no- 0438 517 290
My email- mrdelford@qelvo.com.au
Installation & Decomissioning of aiconditioning split systems
LIC NO: TRK 540316
Nice to have
• Lanterra Electrical & Refrigeration

```html
<!DOCTYPE html>
<html lang="en">
<head>
<meta charset="utf-8">
<title>Lanterra Electrical – Business Card</title>
<link rel="stylesheet" href="https://fonts.googleapis.com/css2?family=Crimson+Text:wght@400;600&display=swap">
<style>
  :root {
    --page: #ffffff;
    --card-top: #2e2e2e;
    --card-bottom: #171717;
    --brand-blue: #1f4e9c;
    --brand-blue-light: #2f63b8;
    --band-blue: #2a78c6;
    --band-deep: #1b5ea6;
    --mark-blue: #3a8fe0;
    --text-light: #e4e4e4;
    --text-muted: #a9a9a9;
    --tagline: #dbe7f5;
    --badge: #f4f6f8;
  }
  * { margin: 0; padding: 0; box-sizing: border-box; }
  html, body {
    width: 1200px; height: 900px; overflow: hidden;
    background: var(--page);
    font-family: "Crimson Text", Georgia, serif;
  }
  .canvas { position: relative; width: 1200px; height: 900px; }

  .card {
    position: absolute;
    overflow: hidden;
    background: linear-gradient(160deg, var(--card-top), var(--card-bottom));
  }

  /* brand lockup: square + stacked name */
  .brand { display: flex; align-items: center; gap: 12px; }
  .brand-square {
    flex: none;
    background: linear-gradient(135deg, var(--mark-blue), var(--brand-blue));
  }
  .brand-name {
    display: flex; flex-direction: column; align-items: flex-end;
    color: var(--brand-blue); font-weight: 400; line-height: 1; white-space: nowrap;
  }
  .brand-name .word-main { display: block; }
  .brand-name .word-sub { display: block; letter-spacing: 0.08em; }

  /* front of card */
  .card-front { left: 55px; top: 70px; width: 600px; height: 350px; }
  .card-front .brand { position: absolute; left: 100px; top: 145px; }
  .card-front .brand-square { width: 56px; height: 56px; }
  .card-front .brand-name { color: var(--brand-blue-light); }
  .card-front .word-main { font-size: 52px; }
  .card-front .word-sub { font-size: 22px; margin-top: -6px; }

  /* back of card */
  .card-back { left: 585px; top: 487px; width: 573px; height: 348px; }
  .card-back .band { position: absolute; inset: 0; }
  .card-back .brand { position: absolute; left: 28px; top: 22px; gap: 8px; }
  .card-back .brand-square { width: 40px; height: 40px; }
  .card-back .brand-name { color: var(--brand-blue-light); }
  .card-back .word-main { font-size: 36px; }
  .card-back .word-sub { font-size: 16px; margin-top: -5px; }

  .holder-name {
    position: absolute; left: 325px; top: 96px;
    font-size: 30px; color: var(--text-light); font-weight: 400;
  }
  .contact {
    position: absolute; left: 30px; top: 166px;
    list-style: none; font-size: 19px; line-height: 27px; color: var(--text-light);
  }
  .contact .label { color: var(--text-muted); margin-right: 6px; }

  .tagline {
    position: absolute; left: 37px; top: 314px;
    font-size: 18px; color: var(--tagline);
  }
  .badge {
    position: absolute; right: 16px; bottom: 14px;
    width: 38px; height: 38px; background: var(--badge);
  }

  /* standalone logo */
  .logo-standalone { position: absolute; left: 25px; top: 632px; gap: 16px; }
  .logo-standalone .brand-square { width: 100px; height: 100px; }
  .logo-standalone .word-main { font-size: 92px; }
  .logo-standalone .word-sub { font-size: 34px; margin-top: -12px; }
</style>
</head>
<body>
<main class="canvas">

  <section class="card card-front" aria-label="Business card front">
    <div class="brand">
      <span class="brand-square"></span>
      <span class="brand-name"><span class="word-main">Lanterra</span><span class="word-sub">Electrical</span></span>
    </div>
  </section>

  <section class="card card-back" aria-label="Business card back">
    <svg class="band" width="573" height="348" viewBox="0 0 573 348" aria-hidden="true">
      <defs>
        <linearGradient id="bandFill" x1="0" y1="0" x2="0" y2="1">
          <stop offset="0" stop-color="#2a78c6"/>
          <stop offset="1" stop-color="#1b5ea6"/>
        </linearGradient>
      </defs>
      <path d="M0 285 C 200 275, 420 250, 573 150 L573 348 L0 348 Z" fill="url(#bandFill)"/>
      <path d="M0 292 C 200 282, 420 257, 573 158" fill="none" stroke="#10253f" stroke-opacity=".5" stroke-width="6"/>
    </svg>

    <div class="brand">
      <span class="brand-square"></span>
      <span class="brand-name"><span class="word-main">Lanterra</span><span class="word-sub">Electrical</span></span>
    </div>

    <h1 class="holder-name">Mark Delford</h1>

    <ul class="contact">
      <li><span class="label">mob:</span> 0438 517 290</li>
      <li><span class="label">email:</span>mrdelford@qelvo.com.au</li>
      <li><span class="label">LIC No:</span>TRK 540316</li>
    </ul>

    <p class="tagline">Installation &amp; Decomissioning of airconditioning Split Systems</p>
    <span class="badge" aria-hidden="true"></span>
  </section>

  <div class="brand logo-standalone" aria-label="Lanterra Electrical logo">
    <span class="brand-square"></span>
    <span class="brand-name"><span class="word-main">Lanterra</span><span class="word-sub">Electrical</span></span>
  </div>

</main>
</body>
</html>
```